Detail Shop Business card design

i need a business card design for my new detailing company called 'Brisk's Polish Works'. i want an all black and white design . simple, direct and to the point. i want the designer to choose a fitting font to match the logothe front should have logo, address, phone and email and the back side should have a slogan and text indicating that we offer services on anything including cars, trucks, motorcycles and RVs. slogan will read "we take pride in your ride"
maybe also very small on the back side the IG icon with Brisks_Polish_Works

phone 208.417.6352
address 3847 E Larkin Ave
Spokane WA 99214
email: BrisksPolish@mailvexo.com

Target Market(s)

all ages , auto enthusiasts

Industry/Entity Type

Automotive

Contact Information for Business Card

the front should have logo, address, phone and email and the back side should have a slogan and text indicating that we offer services on anything including cars, trucks, motorcycles and RVs. slogan will read "we take pride in your ride"

phone 208.417.6352
address 3847 E Larkin Ave
Spokane WA 99214

Colors
000000
ffffff

Requirements
Must have
• bold font and very simple design with good spacing
Nice to have
• anything creative from the designer indicating we service any types of vehicles
Should not have
• any colors ,

```html
<!DOCTYPE html>
<html lang="en">
<head>
<meta charset="utf-8">
<title>Brisk's Polish Works – Business Card</title>
<link rel="stylesheet" href="https://fonts.googleapis.com/css2?family=Roboto+Slab:wght@400;700&display=swap">
<style>
  :root {
    --ink: #ffffff;
    --card: #111111;
    --card-edge: #1c1c1c;
    --backdrop: #2a2a2a;
    --muted: #d9d9d9;
  }
  * { margin: 0; padding: 0; box-sizing: border-box; }
  html, body {
    width: 1200px; height: 900px; overflow: hidden;
    background: var(--backdrop);
    font-family: "Roboto Slab", Georgia, serif;
    color: var(--ink);
  }
  .stage { position: relative; width: 1200px; height: 900px; }
  .card {
    position: absolute;
    width: 720px; height: 411px;
    background: linear-gradient(135deg, var(--card-edge), var(--card));
  }
  .card--back { left: 260px; top: 30px; }
  .card--front { left: 220px; top: 462px; }

  .brand {
    display: flex; align-items: center; gap: 12px;
    font-weight: 700; font-size: 30px; letter-spacing: 1px;
    color: var(--ink); white-space: nowrap;
  }
  .brand-dot {
    width: 22px; height: 22px; border: 3px solid var(--ink); border-radius: 50%;
    flex: none;
  }

  /* back */
  .card--back .brand { position: absolute; left: 0; right: 0; top: 118px; justify-content: center; }
  .slogan {
    position: absolute; left: 0; right: 0; top: 250px;
    display: flex; align-items: center; justify-content: center; gap: 16px;
    font-size: 19px; letter-spacing: 1.5px; text-transform: uppercase;
  }
  .slogan::before, .slogan::after {
    content: ""; width: 60px; height: 1px; background: var(--ink);
  }
  .services {
    position: absolute; left: 0; right: 0; top: 292px; text-align: center;
    font-size: 19px; letter-spacing: 1.5px; text-transform: uppercase;
  }

  /* front */
  .card--front .brand { position: absolute; left: 34px; top: 186px; font-size: 24px; }
  .divider {
    position: absolute; left: 360px; top: 90px; width: 2px; height: 230px; background: var(--ink);
  }
  .contact { position: absolute; left: 400px; top: 100px; }
  .contact-name { font-weight: 400; font-size: 30px; letter-spacing: 2px; text-transform: uppercase; }
  .contact-role { font-size: 16px; color: var(--muted); margin-top: -2px; }
  .contact-address { font-size: 19px; line-height: 1.3; margin-top: 22px; }
  .contact-list { list-style: none; margin-top: 14px; font-size: 19px; line-height: 1.35; }
  .contact-list li { display: flex; align-items: center; gap: 10px; }
  .contact-list svg { width: 12px; height: 12px; flex: none; }
</style>
</head>
<body>
<main class="stage">

  <section class="card card--back" aria-label="Card back">
    <div class="brand"><span class="brand-dot"></span>Brisk's Polish Works</div>
    <p class="slogan">We take pride in your ride</p>
    <p class="services">Cars - Trucks - Motorcycles and RVs</p>
  </section>

  <section class="card card--front" aria-label="Card front">
    <div class="brand"><span class="brand-dot"></span>Brisk's Polish Works</div>
    <div class="divider"></div>
    <div class="contact">
      <h1 class="contact-name">Daniel Reyes</h1>
      <p class="contact-role">Director</p>
      <p class="contact-address">3847 E Larkin Ave<br>Spokane WA 99214</p>
      <ul class="contact-list">
        <li>
          <svg viewBox="0 0 12 12" aria-hidden="true"><path d="M2.5 1 L4.5 1 L5 3.5 L3.8 4.4 Q5 7 7.6 8.2 L8.5 7 L11 7.5 L11 9.5 Q10.5 11 9 11 Q1 9.5 1 3 Q1 1.5 2.5 1 Z" fill="#fff"/></svg>
          208.417.6352
        </li>
        <li>
          <svg viewBox="0 0 12 12" aria-hidden="true"><rect x="0.8" y="2.5" width="10.4" height="7" fill="none" stroke="#fff" stroke-width="1.2"/><path d="M0.8 2.8 L6 6.8 L11.2 2.8" fill="none" stroke="#fff" stroke-width="1.2"/></svg>
          BrisksPolish@mailvexo.com
        </li>
        <li>
          <svg viewBox="0 0 12 12" aria-hidden="true"><circle cx="6" cy="6" r="5" fill="none" stroke="#fff" stroke-width="1.1"/><ellipse cx="6" cy="6" rx="2.2" ry="5" fill="none" stroke="#fff" stroke-width="1"/><path d="M1 6 H11" stroke="#fff" stroke-width="1"/></svg>
          www.BrisksPolish.com
        </li>
      </ul>
    </div>
  </section>

</main>
</body>
</html>
```